Task Description:
I’m wanting a professionally designed 8 ½' x 11, 3 fold brochure, both sides, to print as my target audience are those people who primarily don’t have access to the internet. These items will be dropped off in the mailboxes of all households in the city.
However I do have a web site www.freshtownvoice.ca where I would like to have it as a document that can be down loaded.
This is my first foray into political office and my message needs to be clear, concise and easy to understand. The brochure should be a bit conservative yet be warm and inviting. I’ve selected two pictures that I think make sense under their respective headings, but I'm open to suggestions.I need to update my picture for the front cover.
There is the possibility of having T shirts and business cards made up, which would be in essence a simpler version of the brochure so please keep this in mind. I ask that you work with me and I will compensate you accordingly for the extras should they be required. You may want to consider making the Fresh Town Voice into a logo as we own all the web extensions and have applied for copyright protection for branding purposes.
You may want to look at KL Brightmoor http://www.klbrightmoor.ca/ , or the Pellam Trust of Canada www.pellamtrust.com as two recognizable colour schemes here in Canada but don’t let that limit your imagination.
The content in the flier should remain intact although I am open to some minor suggestions. As you can see my talents as a graphic artist are limited hence my need for that professional make over that will give it a bit of razzle dazzle and set me out from the other candidates. So use your imagination!!
Target Market(s)
Middle age voters who may or may not have access to the internet and still prefer print
Industry/Entity Type
Conservative

```html
<!DOCTYPE html>
<html lang="en">
<head>
<meta charset="utf-8">
<title>Fresh Town Voice – Brochure Inside Spread</title>
<link rel="stylesheet" href="https://fonts.googleapis.com/css2?family=Archivo+Black&family=PT+Sans:wght@400;700&display=swap">
<style>
  :root{
    --sky:#a7aed8;
    --haze:#c9c6dc;
    --sand:#e6dbd1;
    --sand-deep:#d9cbbf;
    --footer:#d3c9c0;
    --ink:#111111;
    --body:#1c1c1c;
    --accent:#3f56a6;
    --rule:#2e3f94;
    --photo-frame:#ffffff;
  }
  *{box-sizing:border-box;margin:0;padding:0}
  html,body{width:1200px;height:908px;overflow:hidden;background:#fff}
  .brochure{
    position:relative;width:1200px;height:908px;overflow:hidden;
    background:linear-gradient(180deg,var(--sky) 0%,var(--haze) 38%,var(--sand) 62%,var(--sand-deep) 92%);
    font-family:"PT Sans",sans-serif;color:var(--body);
  }
  .family-scene{
    position:absolute;left:100px;top:540px;width:640px;height:300px;
    background:radial-gradient(ellipse at 55% 60%,rgba(170,150,135,.35) 0%,rgba(170,150,135,.15) 45%,rgba(170,150,135,0) 72%);
  }
  .panel{position:absolute;top:0}
  .panel--story{left:53px;width:292px}
  .panel--work{left:449px;width:298px}
  .panel--cover{left:850px;width:296px;text-align:center}

  .heading{
    font-family:"Archivo Black",sans-serif;color:var(--ink);
    font-size:32px;line-height:43px;margin-top:22px;white-space:nowrap;
  }
  .heading .accent{color:var(--accent)}
  .copy{font-size:15px;line-height:19.6px;text-align:justify}
  .copy strong{font-weight:700;color:var(--ink)}
  .panel--story .copy{position:absolute;top:140px;left:0;width:292px}
  .copy p+p{margin-top:19.6px}
  .lead strong{font-size:17px}

  .panel--work .copy.intro{margin-top:31px}
  .bus-photo{
    position:absolute;left:1px;top:193px;width:282px;height:212px;
    background:var(--photo-frame);padding:7px;
  }
  .bus-photo .fill{
    width:100%;height:100%;
    background:linear-gradient(180deg,#4f86c8 0%,#9fc0e4 38%,#e9eef2 55%,#8a8f8f 72%,#6d6f6c 100%);
  }
  .panel--work .copy.goal{position:absolute;left:6px;top:417px;width:292px}
  .vote-date,.vote-call{font-family:"Archivo Black",sans-serif;color:var(--ink);text-align:center;position:absolute;left:-40px;width:372px;white-space:nowrap}
  .vote-date{top:605px;font-size:31px;line-height:38px}
  .vote-call{top:664px;font-size:38px;line-height:56px}

  .tagline{margin-top:29px;font-weight:700;line-height:1.25}
  .tagline .t1{font-size:10px;color:var(--ink);letter-spacing:.2px}
  .tagline .t2{font-size:14px;color:var(--accent)}
  .tagline .t3{font-size:16px;color:var(--ink)}
  .cover-name{font-family:"Archivo Black",sans-serif;margin-top:50px;line-height:58px}
  .cover-name .first{font-size:50px;color:var(--ink);display:block}
  .cover-name .last{font-size:44px;color:var(--accent);display:block}
  .portrait{
    position:absolute;left:45px;top:263px;width:202px;height:281px;
    background:linear-gradient(180deg,#d9d9d9 0%,#b9b9b9 45%,#7d7d7d 80%,#2e2e2e 100%);
  }
  .cover-title{position:absolute;left:0;top:575px;width:296px;font-family:"Archivo Black",sans-serif;line-height:50px}
  .cover-title .l1{display:block;font-size:35px;color:var(--ink)}
  .cover-title .l2{display:block;font-size:47px;color:var(--accent)}

  .footer-rule{position:absolute;left:0;top:842px;width:1200px;height:6px;background:var(--rule)}
  .footer-gap{position:absolute;left:0;top:848px;width:1200px;height:5px;background:#f1ece6}
  .footer{
    position:absolute;left:0;top:853px;width:1200px;height:55px;background:var(--footer);
    display:flex;align-items:center;
  }
  .web{position:absolute;font-weight:700;font-size:20px;color:var(--ink);text-align:center;width:320px}
  .web .accent{color:var(--accent)}
  .web--1{left:37px}.web--2{left:418px}.web--3{left:837px}
</style>
</head>
<body>
<main class="brochure">
  <div class="family-scene" role="img" aria-label="Faint silhouette of a family walking hand in hand"></div>

  <section class="panel panel--story">
    <h1 class="heading">Getting to know<br>Fresh <span class="accent">Town</span> Voice</h1>
    <div class="copy">
      <p class="lead"><strong>Glen Ardman</strong> is a life long resident of Harbour Falls.</p>
      <p>My family has served this community and area for more than 100 years.</p>
      <p>-Walter Ross Ardman built and managed the Northgate Elevator.<br>
      - Douglas Reid Ardman managed the Bayline Cement facility<br>
      -Ellen Marsh Ardman was past president of the Chamber of Commerce.<br>
      -Nora Ardman is a champion at the 2010 Provincial Winter Games.</p>
      <p>Although I have a unique vocation through the Quality Assurance Board (QAB) and could live and work anywhere in the world I have chosen to remain and work from Harbour Falls.</p>
      <p>On average I visit and work with more than 30 different corporations a year. I have a high pressure job as companies rely on my skills and expertise to keep them safe and operational. Solving problems, minimizing costs, maximizing production are challenges I face everyday.</p>
    </div>
  </section>

  <section class="panel panel--work">
    <p class="copy intro">I’m currently involved with <strong>Voltaris Dynamics Inc.</strong> a newly created R&amp;D company developing electric propulsion systems for the transit industry. Our research partners consist of faculty and students from <strong>Northshore College.</strong> So I know first hand how difficult it is to start, finance and run a new business in this city.</p>
    <figure class="bus-photo"><div class="fill" role="img" aria-label="Photo of a white and blue hybrid electric transit bus parked outdoors"></div></figure>
    <p class="copy goal">As <strong>Fresh Town Voice,</strong> my goal is to be mayor for two terms, maximum three. With the implementation of a long term plan we will require a fresh face to step forward to complete the process. I also feel that we should reduce the number of city councilors and use those funds to make those positions full time. Term limits should apply to all elected positions!</p>
    <p class="vote-date">On Oct 25th</p>
    <p class="vote-call">Vote<br>Glen Ardman</p>
  </section>

  <section class="panel panel--cover">
    <div class="tagline">
      <div class="t1">UNLOCK THE POTENTIAL</div>
      <div class="t2">OF THE BEST SMALL CITY IN</div>
      <div class="t3">NORTH AMERICA</div>
    </div>
    <h2 class="cover-name"><span class="first">Glen</span><span class="last">ARDMAN</span></h2>
    <div class="portrait" role="img" aria-label="Black and white portrait photo of the candidate"></div>
    <p class="cover-title"><span class="l1">Fresh Town</span><span class="l2">VOICE</span></p>
  </section>

  <div class="footer-rule"></div>
  <div class="footer-gap"></div>
  <footer class="footer">
    <span class="web web--1">www.<span class="accent">fresh</span>town<span class="accent">voice</span>.ca</span>
    <span class="web web--2">www.<span class="accent">fresh</span>town<span class="accent">voice</span>.ca</span>
    <span class="web web--3">www.<span class="accent">fresh</span>town<span class="accent">voice</span>.ca</span>
  </footer>
</main>
</body>
</html>
```